We (R. T. Galvin & Partners, Inc.) are an executive Search firm based in Los Angeles that is exclusively focused in the Med Tech and Health Tech arenas.   I need a logo to communicate that we are a high end search firm, but also that we are focused in the medicine and science arenas called health tech and med tech.  Many of our clients have robotics and artificial intelligence type products, so it is very technology forward.  I tend to gravitate towards clean, sharp aesthetic as opposed to something that is really over the top.
Attached are files with my logo in two different layouts.  In addition to the letterhead and envelope, I also will need an electronic letterhead in Microsoft Word.  I tend to
I look forward to seeing the designs and just let me know if you have any questions.
Dale

```html
<!DOCTYPE html>
<html lang="en">
<head>
<meta charset="utf-8">
<title>R. T. Galvin &amp; Partners, Inc. — Letterhead</title>
<link rel="stylesheet" href="https://fonts.googleapis.com/css2?family=Montserrat:wght@400;500&display=swap">
<style>
  :root {
    --backdrop: #e9e9e9;
    --paper: #ffffff;
    --ink: #111111;
    --brand-blue: #4fa3dc;
    --band-dark: #000000;
    --band-text: #ffffff;
  }
  * { box-sizing: border-box; margin: 0; padding: 0; }
  html, body {
    width: 1200px; height: 1200px; overflow: hidden;
    background: var(--backdrop);
    font-family: "Montserrat", Arial, sans-serif;
  }
  .letterhead {
    position: absolute;
    left: 167px; top: 40px;
    width: 866px; height: 1120px;
    background: var(--paper);
    box-shadow: 0 6px 18px rgba(0,0,0,0.12);
  }
  .brand {
    position: absolute;
    left: 62px; top: 62px;
    display: flex; align-items: center; gap: 22px;
  }
  .brand-dot {
    width: 30px; height: 30px; border-radius: 50%;
    background: var(--brand-blue);
  }
  .brand-name {
    color: var(--ink);
    font-weight: 500;
    line-height: 1;
  }
  .brand-name .primary {
    display: block;
    font-size: 31px;
    letter-spacing: 0.5px;
  }
  .brand-name .secondary {
    display: block;
    margin-top: 7px;
    font-size: 15px;
    letter-spacing: 4.6px;
  }
  .contact-strip {
    position: absolute;
    left: 0; right: 0; top: 1041px;
    height: 58px;
    display: flex; gap: 5px;
  }
  .contact-band {
    height: 100%;
    display: flex; flex-direction: column; justify-content: center;
    color: var(--band-text);
    font-size: 14px; line-height: 19px;
  }
  .contact-band.phones { width: 247px; background: var(--brand-blue); padding-left: 62px; }
  .contact-band.online { width: 367px; background: var(--band-dark); padding-left: 37px; }
  .contact-band.address { flex: 1; background: var(--brand-blue); padding-left: 33px; }
  .contact-line { display: flex; align-items: center; gap: 5px; white-space: nowrap; }
  .contact-line svg { width: 10px; height: 10px; flex: none; }
</style>
</head>
<body>
  <main class="letterhead">
    <header class="brand">
      <span class="brand-dot" aria-hidden="true"></span>
      <div class="brand-name">
        <span class="primary">R. T. GALVIN</span>
        <span class="secondary">&amp; PARTNERS INC.</span>
      </div>
    </header>

    <footer class="contact-strip">
      <div class="contact-band phones">
        <div class="contact-line">
          <svg viewBox="0 0 10 10" aria-hidden="true"><path d="M2 0.8 L3.6 2.6 L2.8 3.6 Q4 6 6.4 7.2 L7.4 6.4 L9.2 8 L8 9.4 Q2.4 8.6 0.6 2 Z" fill="#fff"/></svg>
          <span>+1(213)555-0148</span>
        </div>
        <div class="contact-line">
          <svg viewBox="0 0 10 10" aria-hidden="true"><rect x="2.5" y="0.5" width="5" height="3" fill="#fff"/><rect x="0.5" y="3.5" width="9" height="4" rx="1" fill="#fff"/><rect x="2.5" y="6.5" width="5" height="3" fill="#fff"/></svg>
          <span>+1(213)555-0193</span>
        </div>
      </div>
      <div class="contact-band online">
        <div class="contact-line">
          <svg viewBox="0 0 10 10" aria-hidden="true"><rect x="0.8" y="2" width="8.4" height="6" fill="none" stroke="#fff" stroke-width="1"/><path d="M0.8 2 L5 5.4 L9.2 2" fill="none" stroke="#fff" stroke-width="1"/></svg>
          <span>office@galvinpartners.com</span>
        </div>
        <div class="contact-line">
          <svg viewBox="0 0 10 10" aria-hidden="true"><circle cx="5" cy="5" r="4.2" fill="none" stroke="#fff" stroke-width="0.9"/><ellipse cx="5" cy="5" rx="1.8" ry="4.2" fill="none" stroke="#fff" stroke-width="0.9"/><path d="M0.8 5 H9.2" stroke="#fff" stroke-width="0.9"/></svg>
          <span>www.galvinpartners.com</span>
        </div>
      </div>
      <div class="contact-band address">
        <div class="contact-line"><span>418 Kestrel Avenue</span></div>
        <div class="contact-line"><span>&nbsp;Pasadena, CA 91105</span></div>
      </div>
    </footer>
  </main>
</body>
</html>
```